Website Design for a holiday home letting busines

We require a redesign of our present website www.pinebrookstays.com. We want the website to stand out and look professional and clean to make holiday hunters want to book a caravan or lodge holiday with us. Our logo is red however we DO NOT want the website to be red. We want a natural colour scheme.

The final design should communicate that we are a professional company to book with.

On the home page we require;
Overview of company
Photo
Search box for holiday (check in)
Late Deals
Reviews
News

We would like the following pages designed; home page, available dates page, caravans page, content page.

The website should be responsive for smart phones. One website I do like is http://www.verdoliso.be/nl/

Target Market(s)

Families

Industry/Entity Type

Travel

Number of Pages Required

5+ page

Font styles to use
Serif

Requirements
Must have
• The project must be responsive for mobile phones and tablets.
• Ability to search for holiday home holidays
• We want a natural colour scheme.
Nice to have
• A style we like is http://www.verdoliso.be/nl/
Should not have
• Do not use red as a colour for the website. Our logo is red so this is the only time we want this used.

```html
<!DOCTYPE html>
<html lang="en">
<head>
<meta charset="utf-8">
<title>Pinebrook Stays – Caravans and Lodges</title>
<link href="https://fonts.googleapis.com/css2?family=Open+Sans:wght@400;600;700&display=swap" rel="stylesheet">
<style>
:root{
  --blue:#1d6db5;
  --blue-dark:#0f4f8f;
  --green:#8ea52d;
  --text:#555;
  --muted:#888;
  --card:#f2f2f2;
  --brand:#c8262c;
  --white:#fff;
}
*{box-sizing:border-box;margin:0;padding:0}
html,body{width:818px;height:1200px;overflow:hidden}
body{font-family:"Open Sans",sans-serif;color:var(--text);background:var(--white);font-size:10px}
.page{width:818px;height:1200px;position:relative}
.header{height:62px;display:flex;align-items:center;justify-content:space-between;padding:0 68px}
.brand{display:flex;align-items:center;gap:6px;font-weight:700;font-size:17px;color:var(--brand)}
.brand i{width:14px;height:14px;background:var(--brand);display:block}
.header-right{display:flex;align-items:center;gap:12px}
.enquiry{text-align:right;font-size:8px;color:var(--muted);line-height:1.3}
.enquiry strong{display:block;font-size:12px;color:#333}
.ask{background:var(--brand);color:var(--white);border-radius:14px;padding:6px 14px;font-weight:700;font-size:11px}
.hero{position:relative;height:110px;background:linear-gradient(180deg,#bcd7ec 0%,#dce9f1 45%,#9fae8e 80%,#7c8f6b 100%)}
.nav{position:absolute;top:14px;left:68px;right:68px;height:24px;background:rgba(29,109,181,.85);display:flex;align-items:center;padding:0 10px;gap:22px}
.nav a{color:var(--white);text-decoration:none;font-size:7.5px;font-weight:600;text-transform:uppercase}
.nav a.active{background:var(--white);color:var(--blue);padding:6px 8px}
.intro{padding:20px 68px 0;height:224px}
.intro h1{color:var(--blue);font-size:13.5px;font-weight:700;text-transform:uppercase;margin-bottom:10px}
.intro p{font-size:8px;line-height:1.6;margin-bottom:8px}
.grid{display:grid;grid-template-columns:1fr 1fr;gap:16px 20px;padding:0 68px}
.card{display:flex;background:var(--card);height:136px}
.card .photo{width:150px;flex:none}
.card .info{padding:12px 12px;flex:1}
.card h2{font-size:13px;font-weight:700;color:#333;text-transform:uppercase;margin-bottom:8px}
.spec{display:grid;grid-template-columns:56px 1fr;font-size:7.5px;line-height:1.5}
.spec dt{color:var(--muted)}
.feature{display:flex;align-items:center;gap:6px;font-size:7.5px;margin-top:4px}
.feature span.ico{width:10px;height:10px;background:var(--blue);display:block;border-radius:2px}
.btn{display:inline-block;margin-top:10px;background:var(--green);color:var(--white);font-size:7px;padding:5px 9px}
.ph1{background:linear-gradient(135deg,#d8c9ae,#f2ede3 60%,#9a8a72)}
.ph2{background:linear-gradient(135deg,#a26a3a,#d9a46d 55%,#5d3a1f)}
.ph3{background:linear-gradient(135deg,#e8e2d6,#f7f4ee 50%,#b4a58c)}
.ph4{background:linear-gradient(135deg,#3b3430,#8c7d6a 50%,#d9d2c5)}
.ph5{background:linear-gradient(135deg,#c9bba0,#efe8dc 55%,#7b6d5a)}
.ph6{background:linear-gradient(135deg,#8a6a4a,#e0cbb0 55%,#4b3a2c)}
.footer{position:absolute;top:885px;left:0;right:0;height:280px;background:var(--blue);color:var(--white);display:grid;grid-template-columns:1fr 1fr 1fr;gap:30px;padding:30px 68px 0}
.footer h3{font-size:13px;font-weight:700;text-transform:uppercase;margin-bottom:12px}
.footer p{font-size:7.5px;line-height:1.6;opacity:.9}
.field{background:var(--white);height:20px;margin-top:8px;color:#999;font-size:7px;padding:5px 7px}
.subscribe{display:inline-block;margin-top:10px;background:var(--green);font-size:7.5px;font-weight:700;padding:6px 12px}
.contact-line{display:flex;align-items:center;gap:6px;font-size:8px;margin-top:8px}
.sitemap{display:grid;grid-template-columns:1fr 1fr;row-gap:9px;font-size:7.5px}
.bottom{position:absolute;top:1165px;left:0;right:0;height:35px;background:var(--blue-dark);display:flex;justify-content:space-between;align-items:center;padding:0 68px;color:var(--white);font-size:7px}
.social{display:flex;align-items:center;gap:10px}
.social i{width:14px;height:14px;border-radius:50%;background:var(--white);opacity:.85;display:block}
</style>
</head>
<body>
<div class="page">
  <header class="header">
    <div class="brand"><i></i>Pinebrook Stays</div>
    <div class="header-right">
      <div class="enquiry">GENERAL ENQUIRY<strong>0800 555 0192</strong></div>
      <div class="ask">Questions?</div>
    </div>
  </header>

  <section class="hero" role="img" aria-label="Holiday park landscape with lodges under a blue sky">
    <nav class="nav">
      <a href="#">Home</a><a class="active" href="#">News</a><a href="#">Reviews</a><a href="#">Caravans &amp; Lodges</a><a href="#">Owners</a><a href="#">Alderwick Park</a><a href="#">Late Deals</a><a href="#">Contact Us</a>
    </nav>
  </section>

  <section class="intro">
    <h1>Our caravans and lodges at Alderwick Park Holiday Park</h1>
    <p>We own the caravans and one lakeside lodge at Alderwick Park Holiday Park near Hollin Bay. Our properties sleep at least 6 people, which means bringing all your family and friends is easy. Each one is fitted with TV, heating and a full kitchen, and all are finished to a high standard for your comfort.</p>
    <p>Our accommodation sits in Heron Reach, Maple Row and Willow Bank, with a choice of models to suit your group and budget.</p>
  </section>

  <section class="grid">
    <article class="card"><div class="photo ph1" role="img" aria-label="Bright lodge living room"></div><div class="info"><h2>The Ashford</h2><dl class="spec"><dt>Caravan Type</dt><dd>Lodge</dd><dt>Grade</dt><dd>Luxury Lodge</dd></dl><div class="feature"><span class="ico"></span>Sleeps 6</div><div class="feature"><span class="ico"></span>Bedrooms 3</div><span class="btn">View details</span></div></article>
    <article class="card"><div class="photo ph2" role="img" aria-label="Wood panelled lodge lounge"></div><div class="info"><h2>The Kingsley</h2><dl class="spec"><dt>Caravan Type</dt><dd>Lodge</dd><dt>Grade</dt><dd>Luxury Lodge</dd></dl><div class="feature"><span class="ico"></span>Sleeps 6</div><div class="feature"><span class="ico"></span>Bedrooms 3</div><span class="btn">View details</span></div></article>
    <article class="card"><div class="photo ph3" role="img" aria-label="Caravan lounge with sofas"></div><div class="info"><h2>The Harwood</h2><dl class="spec"><dt>Caravan Type</dt><dd>Lodge</dd><dt>Grade</dt><dd>Luxury Lodge</dd></dl><div class="feature"><span class="ico"></span>Sleeps 6</div><div class="feature"><span class="ico"></span>Bedrooms 3</div><span class="btn">View details</span></div></article>
    <article class="card"><div class="photo ph4" role="img" aria-label="Modern caravan interior with large windows"></div><div class="info"><h2>The Marlow</h2><dl class="spec"><dt>Caravan Type</dt><dd>Lodge</dd><dt>Grade</dt><dd>Luxury Lodge</dd></dl><div class="feature"><span class="ico"></span>Sleeps 6</div><div class="feature"><span class="ico"></span>Bedrooms 3</div><span class="btn">View details</span></div></article>
    <article class="card"><div class="photo ph5" role="img" aria-label="Lodge open plan living area"></div><div class="info"><h2>The Ashford</h2><dl class="spec"><dt>Caravan Type</dt><dd>Lodge</dd><dt>Grade</dt><dd>Luxury Lodge</dd></dl><div class="feature"><span class="ico"></span>Sleeps 6</div><div class="feature"><span class="ico"></span>Bedrooms 3</div><span class="btn">View details</span></div></article>
    <article class="card"><div class="photo ph6" role="img" aria-label="Cosy lodge sitting room"></div><div class="info"><h2>The Kingsley</h2><dl class="spec"><dt>Caravan Type</dt><dd>Lodge</dd><dt>Grade</dt><dd>Luxury Lodge</dd></dl><div class="feature"><span class="ico"></span>Sleeps 6</div><div class="feature"><span class="ico"></span>Bedrooms 3</div><span class="btn">View details</span></div></article>
  </section>

  <footer class="footer">
    <div>
      <h3>Newsletter Signup</h3>
      <p>Join our mailing list to hear about late deals, new lodges and park news first.</p>
      <div class="field">Enter Your Name</div>
      <div class="field">Enter Your Email</div>
      <span class="subscribe">SUBSCRIBE</span>
    </div>
    <div>
      <h3>Contact Information</h3>
      <p>Contact us by phone or email and our friendly team will help you plan your holiday.</p>
      <div class="contact-line"><svg width="10" height="10" viewBox="0 0 10 10"><path d="M2 1h2l1 2-1 1a6 6 0 0 0 2 2l1-1 2 1v2c0 .6-.4 1-1 1A8 8 0 0 1 1 2c0-.6.4-1 1-1z" fill="#fff"/></svg>0800 555 0192</div>
      <div class="contact-line"><svg width="10" height="8" viewBox="0 0 10 8"><rect x=".5" y=".5" width="9" height="7" fill="none" stroke="#fff"/><path d="M.5.5 5 4.5 9.5.5" fill="none" stroke="#fff"/></svg>hello@pinebrookstays.com</div>
    </div>
    <div>
      <h3>Sitemap</h3>
      <div class="sitemap">
        <span>About Us</span><span>Contact Us</span>
        <span>News</span><span>Booking</span>
        <span>Blogs</span><span>Privacy Policy</span>
        <span>2015 Holidays</span><span>Booking Terms</span>
        <span>Late Deals</span><span>Menu</span>
        <span>Local Area</span><span>Site Search</span>
      </div>
    </div>
  </footer>

  <div class="bottom">
    <span>© 2015 Pinebrook Stays. All Rights Reserved.</span>
    <div class="social"><span>Social Icons</span><i></i><i></i><i></i><i></i><i></i></div>
  </div>
</div>
</body>
</html>
```